Concierge Healthcare Business Card Design and Logo

We need a logo and business card design for a new company called "Sound Haven". We will provide concierge audiological care, hearing aids, hearing exams, custom hearing protection etc to patients in the comfort of their homes and offices. We would like a sleek and modern design preferably with an Ear related logo.

Target Market(s)

People with hearing loss, Hunters, Musicians
My usual clientele are older individuals so usually 50+ years old

Industry/Entity Type

Health Care

Contact Information for Business Card

Celia Brandt, AuD
Audiologist
512-648-2917
soundhaven@mailvoro.com
www.soundhaven-vorel.com

Logo Text

Sound Haven

Number of Pages Required

3 page

```html
<!DOCTYPE html>
<html lang="en">
<head>
<meta charset="utf-8">
<title>Sound Haven – Business Card</title>
<link rel="stylesheet" href="https://fonts.googleapis.com/css2?family=Montserrat:wght@400;500;600;700&display=swap">
<style>
  :root {
    --backdrop: #2b2b2d;
    --card-black: #050505;
    --card-white: #ffffff;
    --accent-blue: #1aa3e8;
    --text-white: #ffffff;
    --text-black: #111111;
  }
  * { box-sizing: border-box; margin: 0; padding: 0; }
  html, body {
    width: 1200px; height: 900px; overflow: hidden;
    background: var(--backdrop);
    font-family: "Montserrat", sans-serif;
  }
  .canvas { position: relative; width: 1200px; height: 900px; }
  .card {
    position: absolute; left: 285px; width: 630px; height: 360px;
    border-radius: 22px; overflow: hidden;
    box-shadow: 0 14px 30px rgba(0,0,0,.45);
  }
  /* back side */
  .card-back { top: 60px; background: var(--card-black); }
  .back-brand {
    position: absolute; top: 78px; left: 0; right: 0;
    display: flex; flex-direction: column; align-items: center; gap: 16px;
  }
  .brand-circle {
    width: 120px; height: 120px; border-radius: 50%;
    border: 6px solid var(--accent-blue);
  }
  .back-brand-name {
    color: var(--text-white); font-weight: 600; font-size: 26px;
    letter-spacing: 6px; text-transform: uppercase;
  }
  .back-web {
    position: absolute; bottom: 52px; left: 0; right: 0; text-align: center;
    color: var(--text-white); font-size: 17px; font-weight: 500;
  }
  .back-web .web-core { color: var(--accent-blue); }

  /* front side */
  .card-front { top: 480px; background: var(--card-white); }
  .front-shape { position: absolute; inset: 0; }
  .front-brand {
    position: absolute; left: 40px; top: 150px;
    display: flex; align-items: center; gap: 14px;
  }
  .front-brand .brand-circle { width: 62px; height: 62px; border-width: 4px; }
  .brand-divider { width: 2px; height: 62px; background: var(--text-black); }
  .front-brand-name {
    color: var(--text-black); font-weight: 600; font-size: 24px;
    letter-spacing: 5px; line-height: 1.25; text-transform: uppercase;
  }
  .corner-brand {
    position: absolute; top: 22px; right: 34px;
    width: 104px; height: 104px; border-radius: 50%;
    background: var(--card-white); border: 5px solid var(--accent-blue);
    display: flex; align-items: center; justify-content: center; text-align: center;
    color: var(--text-black); font-weight: 600; font-size: 13px;
    letter-spacing: 2px; line-height: 1.3; text-transform: uppercase;
  }
  .contact {
    position: absolute; right: 30px; top: 146px; text-align: right;
    color: var(--text-white); font-size: 14px; line-height: 1.55;
  }
  .contact-name { color: var(--accent-blue); font-weight: 600; font-size: 18px; }
  .contact-title { margin-bottom: 4px; }
  .contact-line { display: flex; justify-content: flex-end; align-items: center; gap: 8px; }
  .contact-icon { width: 12px; height: 12px; flex: none; }
  .contact-line .spacer { width: 12px; flex: none; }
</style>
</head>
<body>
<main class="canvas">

  <section class="card card-back" aria-label="Business card back">
    <div class="back-brand">
      <div class="brand-circle"></div>
      <span class="back-brand-name">Sound Haven</span>
    </div>
    <p class="back-web">www.<span class="web-core">soundhaven-vorel</span>.com</p>
  </section>

  <section class="card card-front" aria-label="Business card front">
    <svg class="front-shape" viewBox="0 0 630 360" width="630" height="360" aria-hidden="true">
      <path transform="translate(-18,-4)" fill="var(--accent-blue)"
        d="M440 0 C390 60,400 190,290 280 C220 335,100 340,0 350 L0 372 L650 372 L650 0 Z"/>
      <path transform="translate(-10,-2)" fill="var(--card-white)"
        d="M440 0 C390 60,400 190,290 280 C220 335,100 340,0 350 L0 372 L650 372 L650 0 Z"/>
      <path fill="var(--card-black)"
        d="M440 0 C390 60,400 190,290 280 C220 335,100 340,0 350 L0 360 L630 360 L630 0 Z"/>
    </svg>

    <div class="front-brand">
      <div class="brand-circle"></div>
      <div class="brand-divider"></div>
      <div class="front-brand-name">Sound<br>Haven</div>
    </div>

    <div class="corner-brand">Sound<br>Haven</div>

    <div class="contact">
      <p class="contact-line contact-name">Celia Brandt, AuD<span class="spacer"></span></p>
      <p class="contact-line contact-title">Audiologist<span class="spacer"></span></p>
      <p class="contact-line">512-648-2917
        <svg class="contact-icon" viewBox="0 0 12 12"><path fill="var(--accent-blue)" d="M2.5 0.5 L4.5 0.5 L5 3.5 L3.7 4.5 C4.4 6 5.8 7.4 7.5 8.3 L8.5 7 L11.5 7.5 L11.5 9.5 C11.5 10.7 10.6 11.5 9.5 11.5 C4.8 11.2 0.8 7.2 0.5 2.5 C0.5 1.4 1.3 0.5 2.5 0.5 Z"/></svg>
      </p>
      <p class="contact-line">soundhaven@mailvoro.com
        <svg class="contact-icon" viewBox="0 0 12 12"><rect x="0.8" y="2.3" width="10.4" height="7.4" rx="1" fill="none" stroke="var(--accent-blue)" stroke-width="1.3"/><path d="M1 2.8 L6 6.6 L11 2.8" fill="none" stroke="var(--accent-blue)" stroke-width="1.3"/></svg>
      </p>
      <p class="contact-line">www.soundhaven-vorel.com
        <svg class="contact-icon" viewBox="0 0 12 12"><circle cx="6" cy="6" r="5.2" fill="none" stroke="var(--accent-blue)" stroke-width="1.3"/><ellipse cx="6" cy="6" rx="2.2" ry="5.2" fill="none" stroke="var(--accent-blue)" stroke-width="1"/><path d="M0.8 6 H11.2" stroke="var(--accent-blue)" stroke-width="1"/></svg>
      </p>
    </div>
  </section>

</main>
</body>
</html>
```